International business needs business cards

Our company, DRV Ventures Inc. is in the business of supplying a range construction products with particular emphasis on CEMENT. We have developed our own brand - TORVAN SUPPLIES - with which to infiltrate the market. We are launching our brand of cement (TORVAN Type IS Cement) into the Caribbean which is unlike anything this market has ever seen. A monopoly has existed here for the past 60-odd years and the market has now opened to allow the importation of other brands and consumers are anxious and ready for change/improvement. We are very excited to be launching and want to make a great first impression. We will be conducting workshops and seminars (from government level to the hardware store owners) and we want our business card to give us the strong, confident introduction that we need.

Target Market(s)

construction; builders; engineers; home owners

Industry/Entity Type

Construction

Contact Information for Business Card

Marisol Depree
CEO
cell # 1 555 4180736
Ground floor,Lindell Plaza Suite 2734
George Town,Grand Cayman
Cayman Islands,KY1-4823
EMAIL: m.depree@drvventuresinc.example
web site drvventuresinc.example

COMPANY: skype info drv.ventures.example

second card
Yvette Brannock-Depree
CFO
CELL# 1 555 607 3941
George Town,Grand Cayman
Cayman Islands,KY1-4823
EMAIL: y.brannockdepree@drvventuresinc.example
website drvventuresinc.example

Requirements
Must have
• Business cards must display BOTH logos - DRV is the company and TORVAN is the brand.

```html
<!DOCTYPE html>
<html lang="en">
<head>
<meta charset="utf-8">
<title>DRV Ventures Inc. — Business Cards</title>
<link rel="stylesheet" href="https://fonts.googleapis.com/css2?family=Open+Sans:wght@400;600&display=swap">
<style>
  :root {
    --stage: #4a403b;
    --card: #141414;
    --card-edge: #1f1f1f;
    --ink: #e6e6e6;
    --ink-soft: #a9a9a9;
    --accent: #a3181c;
    --rule: #5a5a5a;
  }
  html, body {
    margin: 0;
    width: 1200px;
    height: 814px;
    overflow: hidden;
    background: var(--stage);
    font-family: "Open Sans", Arial, sans-serif;
  }
  .sheet {
    position: relative;
    width: 1200px;
    height: 814px;
    display: flex;
    align-items: center;
    justify-content: center;
    gap: 40px;
  }
  .card {
    width: 540px;
    height: 310px;
    background: var(--card);
    border: 1px solid var(--card-edge);
    box-shadow: 0 14px 30px rgba(0,0,0,.45);
    position: relative;
    box-sizing: border-box;
  }
  /* Front: contact side */
  .card--contact {
    display: grid;
    grid-template-columns: 218px 1px 1fr;
  }
  .brand-mark {
    display: flex;
    align-items: center;
    justify-content: center;
    gap: 10px;
  }
  .brand-mark__dot {
    width: 14px;
    height: 14px;
    border-radius: 50%;
    background: var(--ink-soft);
  }
  .brand-mark__name {
    color: var(--ink-soft);
    font-size: 22px;
    font-weight: 600;
    letter-spacing: 2px;
  }
  .divider {
    background: var(--rule);
    margin: 52px 0;
  }
  .contact {
    padding: 48px 0 0 26px;
    color: var(--ink);
    font-size: 13.5px;
    line-height: 19px;
  }
  .contact__name {
    color: var(--accent);
    font-size: 17px;
    font-weight: 600;
    margin: 0;
    line-height: 22px;
  }
  .contact__role { margin: 0 0 6px; }
  .contact__address { margin: 0 0 8px; font-style: normal; }
  .contact__list { list-style: none; margin: 0; padding: 0; }
  .contact__list li { display: flex; align-items: center; gap: 10px; }
  .contact__list svg { width: 13px; height: 13px; flex: none; }
  /* Back: company side */
  .card--company {
    display: flex;
    flex-direction: column;
    align-items: center;
    justify-content: center;
  }
  .company-mark {
    display: flex;
    align-items: center;
    gap: 14px;
    margin-top: -10px;
  }
  .company-mark__square {
    width: 62px;
    height: 62px;
    background: var(--accent);
  }
  .company-mark__name {
    color: var(--ink);
    font-size: 30px;
    font-weight: 600;
  }
  .company-url {
    margin-top: 48px;
    color: var(--ink-soft);
    font-size: 12px;
    letter-spacing: 3px;
  }
</style>
</head>
<body>
<main class="sheet">
  <section class="card card--contact">
    <div class="brand-mark">
      <span class="brand-mark__dot"></span>
      <span class="brand-mark__name">TORVAN</span>
    </div>
    <div class="divider"></div>
    <div class="contact">
      <h1 class="contact__name">Marisol Depree</h1>
      <p class="contact__role">CEO</p>
      <address class="contact__address">
        Ground floor<br>
        Lindell Plaza Suite 2734<br>
        George Town,Grand Cayman<br>
        Cayman Islands,KY1-4823
      </address>
      <ul class="contact__list">
        <li>
          <svg viewBox="0 0 12 12" aria-hidden="true"><rect x="3" y="0.5" width="6" height="11" rx="1" fill="none" stroke="var(--accent)" stroke-width="1.4"/></svg>
          1 555 4180736
        </li>
        <li>
          <svg viewBox="0 0 12 12" aria-hidden="true"><rect x="0.5" y="2" width="11" height="8" fill="var(--accent)"/><path d="M0.5 2 L6 6.5 L11.5 2" fill="none" stroke="var(--card)" stroke-width="1"/></svg>
          m.depree@drvventuresinc.example
        </li>
        <li>
          <svg viewBox="0 0 12 12" aria-hidden="true"><circle cx="6" cy="6" r="5.5" fill="var(--accent)"/><path d="M0.5 6 H11.5 M6 0.5 C3 3 3 9 6 11.5 C9 9 9 3 6 0.5" fill="none" stroke="var(--card)" stroke-width=".8"/></svg>
          drvventuresinc.example
        </li>
      </ul>
    </div>
  </section>

  <section class="card card--company">
    <div class="company-mark">
      <span class="company-mark__square"></span>
      <span class="company-mark__name">DRV Ventures Inc.</span>
    </div>
    <p class="company-url">www.drvventuresinc.example</p>
  </section>
</main>
</body>
</html>
```